Consulting Company PowerPoint Template Design

We are looking for an updated PowerPoint template design or our 55 person energy consulting firm (K7) based in San Francisco (www.kseven-example.com). We would like two versions of the same PowerPoint template in a 16:9 and 4:3 format with our existing logo.

We have an existing color scheme and template and are seeking your help to polish/update the template design for wide format and create a flexible template that is easy to use with content from Excel and Word. Our current template, and a couple of examples that we like are attached.

Specific requests include:

• Dark background for slide title
• A narrow section header
• Maximizing white space for content
• A limited number of well designed Master template layouts to choose from
• A selection of title and section header slides that are not San Francisco specific with some variety to chose from ideally with a focus on energy or nature, graphics/visuals.

For examples of energy specific templates see:
https://www.brightslidehub.example/energy/powerpoint-templates/0.html

Requirements
Must have
• Must use our logo but open to other designs, fonts, and styles for the PowerPoint template.
• Please use our existing color scheme found in the attached Excel file.
• Also we would like the ability to easily copy and paste from our existing/original template to the new template. In other words we would like backward compatibility to apply the new template format to our old PowerPoints that use our existing template.

```html
<!DOCTYPE html>
<html lang="en">
<head>
<meta charset="utf-8">
<title>K7 Project Title Slide</title>
<link rel="stylesheet" href="https://fonts.googleapis.com/css2?family=Fira+Sans:wght@400;500;600&display=swap">
<style>
  :root {
    --panel-light: #f1f1f1;
    --brand-blue: #064f6e;
    --accent-gold: #c9a35e;
    --title-gold: #f3c77b;
    --text-white: #ffffff;
  }
  html, body {
    margin: 0;
    padding: 0;
    width: 1200px;
    height: 899px;
    overflow: hidden;
    background: var(--panel-light);
  }
  .slide {
    position: relative;
    width: 1200px;
    height: 899px;
    overflow: hidden;
    font-family: "Fira Sans", Arial, sans-serif;
  }
  .side-panel {
    position: absolute;
    left: 0;
    top: 0;
    width: 344px;
    height: 100%;
    background: var(--panel-light);
  }
  .gold-rule {
    position: absolute;
    left: 344px;
    top: 0;
    width: 9px;
    height: 100%;
    background: var(--accent-gold);
  }
  .main-panel {
    position: absolute;
    left: 353px;
    top: 0;
    right: 0;
    height: 100%;
    background: var(--brand-blue);
  }
  .title-block {
    position: absolute;
    right: 131px;
    top: 412px;
    text-align: right;
    color: var(--text-white);
  }
  .project-title {
    margin: 0;
    font-size: 50px;
    font-weight: 500;
    letter-spacing: 0.5px;
    line-height: 1.1;
  }
  .project-title .highlight {
    color: var(--title-gold);
  }
  .project-subtitle {
    margin: 10px 0 0;
    font-size: 29px;
    font-weight: 400;
    line-height: 1.2;
  }
  .brand {
    position: absolute;
    left: 299px;
    top: 724px;
    display: flex;
    align-items: center;
    gap: 16px;
  }
  .brand-dot {
    width: 86px;
    height: 86px;
    border-radius: 50%;
    background: var(--brand-blue);
    border: 3px solid var(--text-white);
    flex: none;
  }
  .brand-name {
    color: var(--text-white);
    font-size: 37px;
    font-weight: 600;
    white-space: nowrap;
  }
</style>
</head>
<body>
  <main class="slide">
    <div class="side-panel"></div>
    <div class="main-panel"></div>
    <div class="gold-rule"></div>

    <section class="title-block">
      <h1 class="project-title"><span class="highlight">PROJECT</span> TITLE HERE</h1>
      <p class="project-subtitle">Subtext here Subtext here</p>
    </section>

    <div class="brand">
      <span class="brand-dot"></span>
      <span class="brand-name">Kestrel+Seven Analytics</span>
    </div>
  </main>
</body>
</html>
```